Private Investigation Business Card Design

I need a business card for a new private investigation company named Brisk Inquiries. I perform mainly surveillance jobs, vehicle repossessions, document serves etc. The final design should aim for a professional look. The logo has a magnifying glass with stick man arms and legs and is in a running action to show the "Brisk" aspect of the name. If the colour scheme could remain the same as the website www.briskinquiries-demo.com.au with silvers,blacks and a couple electric blue highlights.
Industry/Entity Type
Business
Contact Information for Business Card
Morgan Kellaway
Brisk Inquiries
0487316204
PO Box 58, Carnwell NSW 2291
info@briskinquiries-demo.com.au
www.briskinquiries-demo.com.au
Look and feel

```html
<!DOCTYPE html>
<html lang="en">
<head>
<meta charset="utf-8">
<title>Brisk Inquiries – Business Card</title>
<link href="https://fonts.googleapis.com/css2?family=Arimo:wght@400;700&display=swap" rel="stylesheet">
<style>
  :root {
    --backdrop: #2b2b2b;
    --card-white: #ffffff;
    --silver-light: #e4e4e6;
    --silver-mid: #b9b9bc;
    --silver-dark: #9d9da1;
    --ink: #3a3a3a;
    --ink-soft: #555558;
    --rule: #9a9a9a;
    --mark-grey: #8a8a8e;
  }
  * { box-sizing: border-box; margin: 0; padding: 0; }
  html, body {
    width: 1200px; height: 750px; overflow: hidden;
    background: var(--backdrop);
    font-family: "Arimo", Arial, sans-serif;
  }
  .canvas {
    position: relative; width: 1200px; height: 750px;
  }
  .card {
    position: absolute; top: 225px;
    width: 525px; height: 300px;
    box-shadow: 0 14px 30px rgba(0,0,0,.55);
    overflow: hidden;
  }
  /* front side */
  .card-front {
    left: 55px; background: var(--card-white);
  }
  .front-name {
    position: absolute; top: 92px; left: 0; right: 0;
    text-align: center;
    font-size: 38px; font-weight: 700; color: var(--ink);
    letter-spacing: .5px;
  }
  .social-row {
    position: absolute; top: 210px; left: 0; right: 0;
    display: flex; align-items: center; justify-content: center; gap: 6px;
  }
  .social-row .rule {
    height: 1.5px; width: 130px; background: var(--rule);
  }
  .social-row .rule.left { margin-right: 8px; }
  .social-row .rule.right { margin-left: 8px; }
  .social-dot {
    width: 22px; height: 22px; border-radius: 50%;
    background: var(--ink);
  }
  /* back side */
  .card-back {
    left: 620px; display: flex;
  }
  .contact-panel {
    width: 262px; height: 100%;
    background: radial-gradient(circle at 55% 35%, var(--silver-light) 0%, var(--silver-mid) 60%, var(--silver-dark) 100%);
    padding: 62px 0 0 34px;
    color: var(--ink-soft);
    border-right: 1px solid #8c8c8f;
  }
  .contact-name {
    font-size: 21px; font-weight: 700; color: var(--ink);
    margin-bottom: 20px;
  }
  .contact-address {
    font-size: 13px; line-height: 17px; margin-bottom: 14px;
  }
  .contact-list { list-style: none; font-size: 13px; }
  .contact-list li {
    display: flex; align-items: center; gap: 8px;
    margin-bottom: 8px;
  }
  .contact-list svg { width: 13px; height: 13px; flex: none; fill: var(--ink); }
  .logo-panel {
    flex: 1; background: var(--card-white);
    display: flex; align-items: center; justify-content: center;
  }
  .logo-name {
    font-size: 32px; font-weight: 700; color: var(--mark-grey);
  }
</style>
</head>
<body>
<main class="canvas">
  <section class="card card-front" aria-label="Card front">
    <p class="front-name">Brisk Inquiries</p>
    <div class="social-row" aria-label="Social links">
      <span class="rule left"></span>
      <span class="social-dot"></span>
      <span class="social-dot"></span>
      <span class="social-dot"></span>
      <span class="social-dot"></span>
      <span class="rule right"></span>
    </div>
  </section>

  <section class="card card-back" aria-label="Card back">
    <div class="contact-panel">
      <h1 class="contact-name">Morgan Kellaway</h1>
      <p class="contact-address">PO Box 58<br>Carnwell NSW 2291</p>
      <ul class="contact-list">
        <li>
          <svg viewBox="0 0 16 16" aria-hidden="true"><path d="M3 1.5l3 .5 1 3.5-2 1.3a9 9 0 0 0 4.2 4.2l1.3-2 3.5 1 .5 3-1.8 1.5C7 14 2 9 1.5 3.3z"/></svg>
          <span>0487 316 204</span>
        </li>
        <li>
          <svg viewBox="0 0 16 16" aria-hidden="true"><path d="M1 3h14v10H1z M2.2 4.2v.4L8 8.8l5.8-4.2v-.4z" fill-rule="evenodd"/></svg>
          <span>info@briskinquiries-demo.com.au</span>
        </li>
        <li>
          <svg viewBox="0 0 16 16" aria-hidden="true"><circle cx="8" cy="8" r="7"/><path d="M1 8h14M8 1c3 3 3 11 0 14M8 1c-3 3-3 11 0 14" stroke="#c9c9cc" stroke-width="1" fill="none"/></svg>
          <span>www.briskinquiries-demo.com.au</span>
        </li>
      </ul>
    </div>
    <div class="logo-panel">
      <p class="logo-name">Brisk Inquiries</p>
    </div>
  </section>
</main>
</body>
</html>
```